needing web design for aerial and satellite installation comapny

We need our website designing, it needs to be professional and look creative,
We are a aerial and satellite company called Corvid Mend & Reach ()
I like this site design also some of the following maybe:

https://www.skylorn.co.uk/

http://brimwell.co.uk/

http://quillon4guard.co.uk/portfolio/kmt-brimwell/

The design will require coding once the design is complete, i haven't paid for this yet as i want to be sure the design is good before i commit.

The template needs to look professional and look like one of the leading companies.
The site will consist of all the features this site has https://www.skylorn.co.uk/

I like a modern design with the latest technology.

Target Market(s)

tv aerial satellite installation

Industry/Entity Type

Satellite Tv

Number of Pages Required

3 page

Font styles to use
Sans Serif

Colors

Designer to choose colors to be used in the design.

Requirements
Must have
• eb Contest Brief We need our website designing, it needs to be professional and look creative,
• We are a aerial and satellite company called Corvid Mend Reach ()
• I like this site design also some of the following maybe:
• https://www.skylorn.co.uk/
• http://brimwell.co.uk/
• http://quillon4guard.co.uk/portfolio/kmt-brimwell/
• The design will require coding once the design is complete, i haven't paid for this yet as i want to be sure the design is good before i commit.
• The template needs to look professional and look like one of the leading companies.
• The site will consist of all the features this site has https://www.skylorn.co.uk/
• I like a modern design with the latest technology.
Nice to have
• http://brimwell.co.uk/
Should not have
• poor design

```html
<!DOCTYPE html>
<html lang="en">
<head>
<meta charset="utf-8">
<title>Corvid Mend &amp; Reach – Aerial &amp; Satellite Installers</title>
<link rel="stylesheet" href="https://fonts.googleapis.com/css2?family=Roboto:wght@400;500;700&display=swap">
<style>
:root{
  --green:#55c96a;
  --green-light:#6fd482;
  --orange:#f39c1f;
  --ink:#111;
  --text:#333;
  --muted:#666;
  --pale:#eeeeee;
  --faint:#f2f2f2;
  --black:#0d0d0d;
  --footer:#141414;
  --white:#fff;
}
*{box-sizing:border-box;margin:0;padding:0}
html,body{width:1200px;height:3010px;overflow:hidden}
body{font-family:"Roboto",Arial,sans-serif;color:var(--text);background:var(--white);position:relative}
.abs{position:absolute}

/* top bar */
.topbar{left:0;top:0;width:1200px;height:36px;background:var(--black);color:var(--white);font-size:12px}
.topbar__item{top:11px;display:flex;align-items:center;gap:8px}
.social{display:flex;gap:16px}
.social span{width:9px;height:9px;border-radius:50%;background:var(--white);display:block}

/* header + hero */
.hero-bg{left:0;top:36px;width:1200px;height:746px;background:var(--pale)}
.logo{left:200px;top:62px;width:130px;text-align:center;font-size:11px;font-weight:700;letter-spacing:2px;color:var(--ink);display:flex;flex-direction:column;align-items:center;gap:6px}
.logo__mark{width:26px;height:26px;background:var(--ink)}
.nav{left:353px;top:36px;display:flex;height:76px}
.nav a{display:flex;align-items:center;padding:0 7px;font-size:11px;font-weight:700;color:var(--ink);text-decoration:none;white-space:nowrap}
.nav a.is-active{background:var(--green);color:var(--white);padding:0 8px}
.hero-panel{left:0;top:260px;width:1000px;height:450px;background:var(--white)}
.hero-photo{left:480px;top:132px;width:720px;height:518px;background:linear-gradient(135deg,#e9e9e9 0%,#d8d6d3 45%,#b6a79a 70%,#cfcfcf 100%)}
.hero-title{left:200px;top:356px;font-size:60px;font-weight:700;line-height:64px;color:var(--ink);white-space:nowrap;letter-spacing:-1px}
.hero-clip{left:480px;top:356px;width:720px;height:60px;overflow:hidden}
.hero-clip .hero-title{left:-280px;top:0;color:var(--white)}
.hero-rule{left:156px;top:517px;width:74px;height:2px;background:#888}
.hero-text{left:243px;top:508px;width:230px;font-size:11.5px;line-height:17px;color:var(--muted)}
.btn{display:flex;align-items:center;justify-content:center;background:var(--green);color:var(--white);font-size:12px;font-weight:500}
.hero-btn{left:243px;top:563px;width:118px;height:38px}
.dots{display:flex;gap:5px}
.dots span{width:7px;height:7px;background:#ccc}
.dots span.on{background:var(--ink)}

/* section headings */
.ghost{left:0;width:1200px;text-align:center;font-size:54px;font-weight:700;color:var(--faint)}
.sec-title{left:0;width:1200px;text-align:center;font-size:25px;font-weight:700;color:var(--ink)}
.sec-desc{left:420px;width:360px;text-align:center;font-size:12px;line-height:17px;color:var(--text)}

/* timeline */
.tl-line{left:617px;top:1030px;width:2px;height:420px;background:#ddd}
.step{width:52px;height:52px;border-radius:50%;background:#eee;display:flex;align-items:center;justify-content:center;font-size:20px;color:var(--text)}
.step::before{content:"";position:absolute;inset:-4px;border-radius:50%;border:3px solid transparent;border-top-color:var(--orange)}
.step-text{width:300px;font-size:12px;line-height:18px;color:var(--text)}
.step-text h3{font-size:13px;font-weight:700;color:var(--ink);margin-bottom:6px}
.step-text--left{text-align:right}
.step-icon{width:60px;height:60px}
.pager{left:607px;top:1518px;display:flex;gap:6px}
.pager span{width:6px;height:6px;border-radius:50%;background:#ccc}
.pager span.on{background:#555}

/* contact band */
.contact-band{left:0;top:1563px;width:1200px;height:460px;background:radial-gradient(ellipse at 70% 30%,#6b6658 0%,#3a3d40 40%,#1c2230 100%)}
.contact-title{left:0;top:1618px;width:1200px;text-align:center;color:var(--white);font-size:22px;font-weight:700;line-height:30px}
.ring{width:116px;height:116px;border-radius:50%;border:2px solid rgba(255,255,255,.7);color:var(--white);display:flex;flex-direction:column;align-items:center;justify-content:center;font-size:12px;gap:4px}
.ring b{font-size:14px}
.ring-link{left:572px;top:1812px;width:62px;height:1px;background:rgba(255,255,255,.5)}
.contact-btn{left:540px;top:1906px;width:118px;height:38px}

/* why us */
.services-box{left:582px;top:2254px;width:418px;height:436px;background:var(--pale)}
.trust{left:195px;top:2216px;width:427px;height:413px;background:var(--green);color:var(--white)}
.trust__title{position:absolute;left:18px;top:56px;font-size:20px;font-weight:500;display:flex;align-items:center;gap:14px}
.trust__title::after{content:"";width:70px;height:2px;background:var(--white)}
.trust__grid{position:absolute;left:21px;top:106px;width:386px;height:263px;display:grid;grid-template-columns:repeat(3,1fr);grid-template-rows:repeat(2,1fr)}
.trust__cell{display:flex;flex-direction:column;align-items:center;justify-content:center;gap:10px;text-align:center;font-size:11px;font-weight:700;line-height:14px;border-right:1px solid rgba(255,255,255,.25);border-bottom:1px solid rgba(255,255,255,.25);padding:0 8px}
.trust__cell:nth-child(3n){border-right:none}
.trust__cell:nth-child(n+4){border-bottom:none}
.trust__cell.is-hover{background:var(--green-light)}
.trust__cell svg{width:44px;height:44px}
.svc-title{left:656px;top:2362px;font-size:22px;font-weight:500;color:var(--ink);display:flex;align-items:center;gap:14px}
.svc-title::after{content:"";width:74px;height:2px;background:var(--ink)}
.svc-text{left:656px;top:2406px;width:320px;font-size:12px;line-height:18px;color:var(--text)}
.svc-btn{left:656px;top:2601px;width:166px;height:36px}

/* footer */
.footer{left:0;top:2770px;width:1200px;height:200px;background:var(--footer);color:var(--white)}
.footer h4{position:absolute;top:40px;font-size:22px;font-weight:400}
.footer .sub{position:absolute;top:76px;font-size:11px;color:#888;letter-spacing:.5px}
.f-line{position:absolute;left:195px;display:flex;align-items:center;gap:14px;font-size:12px;color:#bbb}
.f-social{position:absolute;left:478px;top:110px;display:flex;gap:22px}
.f-social span{width:9px;height:9px;border-radius:50%;background:var(--white);display:block}
.news{position:absolute;left:688px;top:96px;width:312px;height:40px;display:flex}
.news__input{flex:1;background:var(--green);color:var(--white);font-size:11px;display:flex;align-items:center;padding-left:18px}
.news__btn{width:104px;background:var(--white);color:var(--green);font-size:11px;display:flex;align-items:center;justify-content:center}
.copyright{left:0;top:2970px;width:1200px;height:40px;background:var(--black);color:var(--white);font-size:11px;display:flex;align-items:center;justify-content:center}
</style>
</head>
<body>

<!-- top bar -->
<div class="abs topbar">
  <div class="abs topbar__item" style="left:200px">
    <svg width="13" height="13" viewBox="0 0 24 24" fill="#fff"><path d="M6.6 10.8a15 15 0 0 0 6.6 6.6l2.2-2.2c.3-.3.7-.4 1-.2 1.1.4 2.3.6 3.6.6.6 0 1 .4 1 1V20c0 .6-.4 1-1 1A17 17 0 0 1 3 4c0-.6.4-1 1-1h3.5c.6 0 1 .4 1 1 0 1.3.2 2.5.6 3.6.1.3 0 .7-.2 1z"/></svg>
    1-800-555-0142
  </div>
  <div class="abs topbar__item" style="left:336px">
    <svg width="14" height="11" viewBox="0 0 24 18" fill="none" stroke="#fff" stroke-width="2"><rect x="1" y="1" width="22" height="16"/><path d="M1 1l11 9 11-9"/></svg>
    info@corvidmendreach.com
  </div>
  <div class="abs topbar__item social" style="left:912px"><span></span><span></span><span></span><span></span></div>
</div>

<!-- header / hero -->
<div class="abs hero-bg"></div>
<div class="abs logo"><div class="logo__mark"></div>CORVID REACH &amp; MEND</div>
<nav class="abs nav">
  <a class="is-active">Home</a><a>TV Aerial Services</a><a>Halcyon Satellite TV</a><a>Smart Home</a><a>CCTV &amp; Alarm</a><a>Wi-Fi Home</a><a>Sound &amp; Vision</a><a>Communal TV</a>
</nav>
<div class="abs hero-panel"></div>
<div class="abs hero-photo" role="img" aria-label="Photo of a couple relaxing on a white sofa watching a wall-mounted television"></div>
<h1 class="abs hero-title">Welcome To Corvid Reach<br>And Mend</h1>
<div class="abs hero-clip" aria-hidden="true"><div class="abs hero-title">Welcome To Corvid Reach</div></div>
<div class="abs hero-rule"></div>
<p class="abs hero-text">Lorem Ipsum is simply dummy text of the printing industry.</p>
<div class="abs btn hero-btn">Contact Us</div>
<div class="abs dots" style="left:482px;top:671px"><span></span><span></span><span></span><span class="on"></span></div>

<!-- installers -->
<div class="abs ghost" style="top:832px">Smart Home &amp; Satellite Installers</div>
<h2 class="abs sec-title" style="top:868px">Smart Home &amp; Satellite Installers</h2>
<p class="abs sec-desc" style="top:906px">Lorem Ipsum is simply dummy text of the printing and typesetting industry. Lorem Ipsum dummy text</p>

<div class="abs tl-line"></div>

<svg class="abs step-icon" style="left:444px;top:975px" viewBox="0 0 60 60" fill="none" stroke="#333" stroke-width="3"><path d="M22 8l8 8 8-8"/><rect x="6" y="16" width="48" height="34" rx="3"/><rect x="12" y="22" width="26" height="22"/><circle cx="46" cy="26" r="2"/><circle cx="46" cy="36" r="2"/><path d="M14 50v5M46 50v5"/></svg>
<div class="abs step" style="left:592px;top:981px">1</div>
<div class="abs step-text" style="left:678px;top:974px"><h3>TV Aerial Services</h3>Lorem Ipsum is simply dummy text of the printing and typesetting industry try's standard dummy text...</div>

<div class="abs step-text step-text--left" style="left:226px;top:1124px"><h3>Halcyon Satellite TV</h3>Lorem Ipsum is simply dummy text of the printing and typesetting industry try's standard dummy text...</div>
<div class="abs step" style="left:592px;top:1132px">2</div>
<svg class="abs step-icon" style="left:676px;top:1124px" viewBox="0 0 60 60" fill="#333"><path d="M12 14a22 22 0 0 0 30 30z"/><path d="M28 30l12-12" stroke="#333" stroke-width="3"/><circle cx="42" cy="16" r="3"/><path d="M24 40l-8 16h20l-6-12z"/></svg>

<svg class="abs step-icon" style="left:444px;top:1276px" viewBox="0 0 60 60" fill="none" stroke="#333" stroke-width="2.5"><rect x="4" y="4" width="52" height="52" rx="4" stroke="#999"/><path d="M8 22c6-8 18-8 24 0-6 8-18 8-24 0z"/><circle cx="20" cy="22" r="4" fill="#333"/><path d="M36 46V28l14-4v18"/><circle cx="32" cy="46" r="4" fill="#333"/><circle cx="46" cy="42" r="4" fill="#333"/></svg>
<div class="abs step" style="left:592px;top:1283px">3</div>
<div class="abs step-text" style="left:678px;top:1275px"><h3>Sound &amp; Vision</h3>Lorem Ipsum is simply dummy text of the printing and typesetting industry try's standard dummy text...</div>

<div class="abs step-text step-text--left" style="left:226px;top:1425px"><h3>Smart Home Systems</h3>Lorem Ipsum is simply dummy text of the printing and typesetting industry try's standard dummy text...</div>
<div class="abs step" style="left:592px;top:1433px">4</div>
<svg class="abs step-icon" style="left:676px;top:1424px" viewBox="0 0 60 60" fill="none" stroke="#333" stroke-width="3"><path d="M6 28L30 6l24 22"/><path d="M12 24v30h36V24"/><path d="M22 40a11 11 0 0 1 16 0M26 44a5 5 0 0 1 8 0"/><circle cx="30" cy="48" r="2" fill="#333"/></svg>

<div class="abs pager"><span class="on"></span><span></span></div>

<!-- contact band -->
<div class="abs contact-band" role="img" aria-label="Photo of large satellite dishes against a dusky blue sky"></div>
<h2 class="abs contact-title">Contact Corvid Mend &amp; Reach Today - For<br>Same Day Service</h2>
<svg class="abs" style="left:582px;top:1698px" width="36" height="48" viewBox="0 0 36 48" fill="var(--orange)"><rect x="8" y="6" width="20" height="34" rx="3" transform="rotate(-18 18 23)"/><path d="M4 6a10 10 0 0 1 8-6M0 10a16 16 0 0 1 10-10" stroke="var(--orange)" stroke-width="2" fill="none"/></svg>
<div class="abs ring" style="left:456px;top:1754px"><b>Free Phone</b>1-800-555-0142</div>
<div class="abs ring-link"></div>
<div class="abs ring" style="left:634px;top:1754px"><b>Mobile No.</b>+1555010293</div>
<div class="abs btn contact-btn">Contact Us</div>

<!-- why us -->
<div class="abs ghost" style="top:2090px">Why Use Corvid Mend &amp; Reach</div>
<h2 class="abs sec-title" style="top:2128px">Why Use Corvid Mend &amp; Reach</h2>

<div class="abs services-box"></div>
<div class="abs trust">
  <div class="trust__title">Trust &amp; Reliability</div>
  <div class="trust__grid">
    <div class="trust__cell is-hover">
      <svg viewBox="0 0 48 48" fill="#fff"><rect x="4" y="18" width="28" height="18"/><path d="M32 22h8l6 8v6H32z"/><circle cx="12" cy="38" r="4"/><circle cx="38" cy="38" r="4"/><path d="M14 16l6-10 6 10" stroke="#fff" stroke-width="2" fill="none"/></svg>
      Same Day TV Aerial Installations</div>
    <div class="trust__cell">
      <svg viewBox="0 0 48 48" fill="#fff"><circle cx="24" cy="18" r="13"/><circle cx="24" cy="18" r="5" fill="var(--green)"/><path d="M20 30l-4 16 8-4 8 4-4-16z"/></svg>
      Local Friendly &amp; Quali -fied Engineers</div>
    <div class="trust__cell">
      <svg viewBox="0 0 48 48" fill="#fff"><rect x="6" y="4" width="26" height="38" rx="2"/><rect x="10" y="8" width="18" height="8" fill="var(--green)"/><circle cx="36" cy="34" r="10" stroke="var(--green)" stroke-width="2"/></svg>
      Free No Obligation Estimates</div>
    <div class="trust__cell">
      <svg viewBox="0 0 48 48" fill="#fff"><path d="M4 44V22l10 6v-6l10 6v-6l10 6V8h8v36z"/></svg>
      Industry Approved</div>
    <div class="trust__cell">
      <svg viewBox="0 0 48 48" fill="#fff"><path d="M2 20l10-8 12 6 12-6 10 8-10 12-6 6-6-4-6 4z"/></svg>
      Our Best Value Promise</div>
    <div class="trust__cell">
      <svg viewBox="0 0 48 48" fill="#fff"><rect x="6" y="4" width="36" height="30" rx="2"/><circle cx="30" cy="32" r="8" stroke="var(--green)" stroke-width="2"/><path d="M26 38l-2 8 6-3 6 3-2-8"/></svg>
      5 Year Installation Warranty</div>
  </div>
</div>

<h3 class="abs svc-title">Our Services</h3>
<p class="abs svc-text">Lorem Ipsum is simply dummy text of the printing and typesetting industry. Lorem Ipsum has been the industry's standard dummy text ever since the 1500s,when an unknown printer took a galley of type and scrambled it to make a type specimen book. It has survived not only fivecenturies, but also the leap int electronic typesetting, remaining essentially unchanged.</p>
<div class="abs btn svc-btn">View Our Services</div>

<!-- footer -->
<footer class="abs footer">
  <h4 style="left:195px">Contact Us</h4>
  <div class="f-line" style="top:106px">
    <svg width="12" height="12" viewBox="0 0 24 24" fill="#bbb"><path d="M6.6 10.8a15 15 0 0 0 6.6 6.6l2.2-2.2c.3-.3.7-.4 1-.2 1.1.4 2.3.6 3.6.6.6 0 1 .4 1 1V20c0 .6-.4 1-1 1A17 17 0 0 1 3 4c0-.6.4-1 1-1h3.5c.6 0 1 .4 1 1 0 1.3.2 2.5.6 3.6.1.3 0 .7-.2 1z"/></svg>+1555010293</div>
  <div class="f-line" style="top:134px">
    <svg width="13" height="10" viewBox="0 0 24 18" fill="#bbb"><path d="M0 0h24v18H0z"/><path d="M0 0l12 9 12-9" stroke="#141414" stroke-width="2" fill="none"/></svg>info@corvidmendreach.com</div>

  <h4 style="left:455px">Connect With Us</h4>
  <div class="sub" style="left:459px">SOCIAL MEDIA CHANNELS</div>
  <div class="f-social"><span></span><span></span><span></span><span></span></div>

  <h4 style="left:688px">Newsletter</h4>
  <div class="sub" style="left:688px">SIGN UP FOR SPECIAL OFFERS</div>
  <div class="news"><div class="news__input">EMAIL</div><div class="news__btn">SUBSCRIBE</div></div>
</footer>
<div class="abs copyright">© Copyright 2018. Corvid Mend &amp; Reach. All Rights Reserved.</div>

</body>
</html>
```